Business cards for 3 Realtors at one brokerage

We will need a business card template that can be projected on 3 business cards. Harborline Realty & Investment Corp. has 3 realtors on staff Dane, Owen, and Miles. We all want a business card that shows our new logo and information. I will attach many versions of our Logo as well as head shots for each realtor (Owen- Long hair, youngest. Miles- Suit jacket, parted hair cut. Dane- Angled Pose, Shirt and Tie.) I have attached our information below.

Dane Foskett
801-555-0147
dane@harborlinehomesite.com
Principal Broker

Miles Tandrow
801-555-0162
miles@harborlinehomesite.com
Real Estate Agent

Owen Tandrow
801-555-0138
owen@harborlinehomesite.com
Real Estate Agent

Harborline Realty & Investment Corp.
HarborlineHomesite.com
5286 N 7200 Suite 208-617, South Jordan, UT 84009

Please feel free to reach out with any questions, comments, or concerns.

```html
<!DOCTYPE html>
<html lang="en">
<head>
<meta charset="utf-8">
<title>Harborline Realty – Business Card</title>
<link href="https://fonts.googleapis.com/css2?family=Montserrat:wght@400;500;600&display=swap" rel="stylesheet">
<style>
  :root {
    --bg: #9a9a9c;
    --brand-blue: #29a3f3;
    --card-white: #ffffff;
    --card-dark: #2c2c2e;
    --card-dark-2: #3a3a3d;
    --ink: #4a4a4a;
    --ink-soft: #6b6b6b;
    --photo: #b9b7b4;
    --back-text: #cfcfd1;
  }
  * { box-sizing: border-box; margin: 0; padding: 0; }
  html, body { width: 1200px; height: 800px; overflow: hidden; }
  body {
    background: var(--bg);
    font-family: "Montserrat", sans-serif;
    display: flex;
    flex-direction: column;
    align-items: center;
    justify-content: center;
    gap: 40px;
  }
  .card {
    position: relative;
    width: 560px;
    height: 320px;
    border-radius: 18px;
    overflow: hidden;
    box-shadow: 0 10px 24px rgba(0,0,0,0.25);
  }

  /* Front */
  .card-front {
    background: var(--card-white);
    border-bottom: 4px solid var(--brand-blue);
  }
  .front-brand {
    position: absolute;
    top: 50%;
    right: 40px;
    transform: translateY(-60%);
    display: flex;
    align-items: center;
    gap: 12px;
    color: var(--brand-blue);
    font-weight: 600;
    font-size: 30px;
    letter-spacing: 0.05em;
  }
  .front-brand .brand-dot {
    width: 22px;
    height: 22px;
    border-radius: 50%;
    background: var(--brand-blue);
  }
  .agent {
    position: absolute;
    left: 30px;
    top: 34px;
    width: 250px;
  }
  .agent-photo {
    width: 92px;
    height: 84px;
    border-radius: 12px;
    background: linear-gradient(160deg, #c4c2bf, var(--photo) 60%, #8f8a86);
    margin-bottom: 12px;
  }
  .agent-name {
    color: var(--brand-blue);
    font-weight: 600;
    font-size: 16px;
    letter-spacing: 0.05em;
    text-transform: uppercase;
    line-height: 1.15;
  }
  .agent-title {
    color: var(--ink-soft);
    font-size: 11px;
    margin-bottom: 6px;
  }
  .agent-address, .agent-contact {
    color: var(--ink);
    font-size: 11px;
    line-height: 1.45;
    list-style: none;
  }
  .agent-address { margin-bottom: 4px; }
  .agent-contact li { display: flex; align-items: center; gap: 7px; }
  .agent-contact svg { width: 10px; height: 10px; flex-shrink: 0; }

  /* Back */
  .card-back {
    background: linear-gradient(135deg, var(--card-dark-2), var(--card-dark) 60%);
    border-bottom: 4px solid var(--brand-blue);
    display: flex;
    flex-direction: column;
    align-items: center;
    justify-content: center;
    gap: 18px;
    color: var(--back-text);
    font-weight: 500;
  }
  .back-circle {
    width: 78px;
    height: 78px;
    border-radius: 50%;
    border: 3px solid var(--back-text);
  }
  .back-name { text-align: center; text-transform: uppercase; }
  .back-name .line-main { font-size: 32px; letter-spacing: 0.05em; }
  .back-name .line-sub { font-size: 13px; letter-spacing: 0.3em; margin-top: 4px; }
</style>
</head>
<body>

  <section class="card card-front">
    <div class="front-brand">
      <span class="brand-dot"></span>
      <span>HARBORLINE</span>
    </div>

    <div class="agent">
      <div class="agent-photo" role="img" aria-label="Headshot of Miles Tandrow"></div>
      <h1 class="agent-name">Miles Tandrow</h1>
      <p class="agent-title">Real Estate Agent</p>
      <p class="agent-address">
        Harborline Realty &amp; Investment Corp.<br>
        5286 N 7200 Suite 208-617<br>
        Cedar Hollow, UT 84099
      </p>
      <ul class="agent-contact">
        <li>
          <svg viewBox="0 0 12 12"><path fill="var(--brand-blue)" d="M2.5 1l2 2.3-1 1.2c.7 1.5 1.8 2.6 3.2 3.3l1.1-1 2.2 2-1 1.2C5.5 10 2 6.5 1.5 2.3z"/></svg>
          801-555-0162
        </li>
        <li>
          <svg viewBox="0 0 12 12"><rect x="1" y="2.5" width="10" height="7" rx="1" fill="var(--brand-blue)"/><path d="M1.5 3l4.5 3.5L10.5 3" stroke="#fff" stroke-width="1" fill="none"/></svg>
          miles@harborlinehomesite.com
        </li>
        <li>
          <svg viewBox="0 0 12 12"><circle cx="6" cy="6" r="5" fill="var(--brand-blue)"/><path d="M1 6h10M6 1c-2 2.8-2 7.2 0 10M6 1c2 2.8 2 7.2 0 10" stroke="#fff" stroke-width=".8" fill="none"/></svg>
          www.HarborlineHomesite.com
        </li>
      </ul>
    </div>
  </section>

  <section class="card card-back">
    <span class="back-circle"></span>
    <div class="back-name">
      <div class="line-main">Harborline Realty</div>
      <div class="line-sub">&amp; Investment Corp.</div>
    </div>
  </section>

</body>
</html>
```